Veltrano.co - Polar Expeditions Specialists

We need a modern, visually striking business card for Veltrano.co, a company specialized in selling expedition cruises to the most remote regions on Earth, with a focus on the Arctic and Antarctica. The design should instantly communicate that the cardholder is an expert in polar travel. Use clean, premium aesthetics with cool tones like icy blue and white, possibly incorporating polar imagery (ice, glaciers, penguins, etc.)

Attached the logo

Contact Information for Business Card

Feels high-end and trustworthy.. Visually memorable — encourages people to keep it

Colors
0054AA
0677BA
7BADD7
CADEEF
E8F1F8

Requirements
Must have
• ice, glaciers, penguins, montains
Nice to have
• modern, transparente,

```html
<!DOCTYPE html>
<html lang="en">
<head>
<meta charset="UTF-8">
<title>Veltrano.co – Business Card</title>
<link href="https://fonts.googleapis.com/css2?family=Jost:wght@400;500;600&family=Poppins:wght@600;700&display=swap" rel="stylesheet">
<style>
  :root {
    --bg: #2b2c2e;
    --card-white: #f7f8f9;
    --navy: #131634;
    --brand-blue: #2a6fb0;
    --ink: #3a3a3c;
    --divider: #b9bcc0;
    --sky-top: #9fb2c6;
    --sky-mid: #c4ccd6;
    --sky-warm: #e6d8c6;
    --cloud: #f1f3f5;
    --snow: #e4eaf0;
    --rock-light: #8b9aab;
    --rock: #3f4a58;
    --sea: #5d666e;
    --sea-deep: #4a5259;
  }
  * { margin: 0; padding: 0; box-sizing: border-box; }
  html, body { width: 1200px; height: 900px; overflow: hidden; }
  body { background: var(--bg); position: relative; font-family: "Jost", sans-serif; }

  .card {
    position: absolute;
    width: 560px;
    height: 320px;
    border-radius: 2px;
    overflow: hidden;
    box-shadow: 0 14px 30px rgba(0,0,0,.45);
  }

  /* Front */
  .card--front { left: 130px; top: 80px; }
  .front__scene {
    position: absolute; inset: 0;
    background: linear-gradient(172deg,
      var(--sky-top) 0%,
      var(--sky-mid) 12%,
      var(--sky-warm) 24%,
      #d9dde3 34%,
      var(--cloud) 42%,
      var(--snow) 50%,
      #c9d3dd 56%,
      var(--rock-light) 62%,
      var(--rock) 70%,
      #707b86 75%,
      var(--sea) 80%,
      var(--sea-deep) 100%);
  }
  .front__brand {
    position: absolute; left: 70px; top: 78px; width: 330px;
    text-align: center; color: var(--navy);
    font-family: "Poppins", sans-serif;
  }
  .front__mark {
    display: block; margin: 0 auto 10px;
    width: 54px; height: 54px; border-radius: 50%;
    background: var(--navy);
  }
  .front__name { font-size: 46px; font-weight: 700; line-height: 1; letter-spacing: .3px; }
  .front__tagline { font-size: 13px; font-weight: 600; margin-top: 6px; }

  /* Back */
  .card--back { left: 510px; top: 500px; background: linear-gradient(100deg, #ffffff 0%, var(--card-white) 60%, #eceef0 100%); }
  .back__brand {
    position: absolute; left: 0; top: 0; width: 245px; height: 100%;
    display: flex; flex-direction: column; align-items: center; justify-content: center; gap: 14px;
  }
  .back__mark { width: 96px; height: 96px; border-radius: 50%; background: var(--brand-blue); }
  .back__name { font-size: 30px; font-weight: 600; color: var(--brand-blue); }
  .back__divider { position: absolute; left: 245px; top: 26px; bottom: 26px; width: 1px; background: var(--divider); }

  .back__details { position: absolute; left: 275px; top: 50px; color: var(--ink); }
  .holder__name { font-size: 21px; font-weight: 600; color: var(--brand-blue); letter-spacing: .5px; line-height: 1.05; }
  .holder__role { font-size: 17px; line-height: 1.2; }
  .contact { list-style: none; margin-top: 22px; font-size: 17px; line-height: 1.55; }
  .contact li { display: flex; align-items: center; gap: 8px; }
  .contact svg { width: 15px; height: 15px; fill: var(--brand-blue); flex: none; }
  .address { margin-top: 18px; margin-left: 24px; font-size: 17px; line-height: 1.2; }
</style>
</head>
<body>

  <section class="card card--front">
    <div class="front__scene" role="img" aria-label="Photograph of snow-covered Antarctic mountains and glaciers wrapped in low cloud, rising from a grey polar sea under a pale sky"></div>
    <div class="front__brand">
      <span class="front__mark"></span>
      <div class="front__name">Veltrano.co</div>
      <div class="front__tagline">Polar Expeditions Specialists</div>
    </div>
  </section>

  <section class="card card--back">
    <div class="back__brand">
      <span class="back__mark"></span>
      <div class="back__name">Veltrano.co</div>
    </div>
    <div class="back__divider"></div>

    <div class="back__details">
      <div class="holder__name">MARA LINDQVIST</div>
      <div class="holder__role">Expeditions Specialists</div>

      <ul class="contact">
        <li>
          <svg viewBox="0 0 24 24"><path d="M6.6 10.8a15.1 15.1 0 0 0 6.6 6.6l2.2-2.2c.3-.3.7-.4 1-.2 1.1.4 2.3.6 3.6.6.6 0 1 .4 1 1V20c0 .6-.4 1-1 1A17 17 0 0 1 3 4c0-.6.4-1 1-1h3.5c.6 0 1 .4 1 1 0 1.3.2 2.5.6 3.6.1.3 0 .7-.2 1z"/></svg>
          300-415-7720
        </li>
        <li>
          <svg viewBox="0 0 24 24"><path d="M2 5h20v14H2z M2 5l10 8 10-8" stroke="#fff" stroke-width="1.5"/></svg>
          mara@veltrano.co
        </li>
        <li>
          <svg viewBox="0 0 24 24"><circle cx="12" cy="12" r="10"/><path d="M2 12h20M12 2c3 3 3 17 0 20M12 2c-3 3-3 17 0 20" stroke="#fff" stroke-width="1.2" fill="none"/></svg>
          www.veltrano.co
        </li>
      </ul>

      <div class="address">00 dummy city<br>dummy place 0000</div>
    </div>
  </section>

</body>
</html>
```